Rollers & Glides.com

Vertical Business Card with focus on branding with our icon. Information on card will be logo, persons name, position, phone number, email address and website. Use the the name Marcus Pellow, position President, phone number 480.915.2267, email Marcus@rollersandglides-demo.com, website www.rollersandglides-demo.com.

```html
<!DOCTYPE html>
<html lang="en">
<head>
<meta charset="UTF-8">
<title>Rollers &amp; Glides.com — Business Card</title>
<link rel="stylesheet" href="https://fonts.googleapis.com/css2?family=Montserrat:wght@400;500;700&family=Roboto:wght@500&display=swap">
<style>
  :root {
    --backdrop: #e6e7e9;
    --brand-blue: #1f4b9f;
    --brand-blue-light: #5a78c4;
    --card-white: #ffffff;
    --text-grey: #4a4b4d;
    --title-grey: #6d6e70;
  }
  * { margin: 0; padding: 0; box-sizing: border-box; }
  html, body {
    width: 1200px;
    height: 1200px;
    overflow: hidden;
    background: var(--backdrop);
  }
  .stage {
    position: relative;
    width: 1200px;
    height: 1200px;
  }
  .card {
    position: absolute;
    top: 230px;
    width: 424px;
    height: 740px;
  }
  .card-front {
    left: 162px;
    background: var(--card-white);
    text-align: center;
    font-family: "Montserrat", sans-serif;
  }
  .card-back {
    left: 614px;
    background: var(--brand-blue);
    overflow: hidden;
  }
  .person-name {
    position: absolute;
    top: 76px;
    width: 100%;
    font-weight: 700;
    font-size: 33px;
    letter-spacing: 0.5px;
    color: var(--brand-blue);
  }
  .person-title {
    position: absolute;
    top: 118px;
    width: 100%;
    font-family: "Roboto", sans-serif;
    font-weight: 500;
    font-size: 29px;
    color: var(--title-grey);
  }
  .brand-lockup {
    position: absolute;
    top: 318px;
    left: 0;
    width: 100%;
    display: flex;
    flex-direction: column;
    align-items: center;
    gap: 18px;
  }
  .brand-dot {
    width: 58px;
    height: 58px;
    border-radius: 50%;
    background: var(--brand-blue);
  }
  .brand-name {
    font-weight: 700;
    font-size: 30px;
    color: var(--brand-blue);
  }
  .contact-icons {
    position: absolute;
    top: 540px;
    width: 100%;
    display: flex;
    justify-content: center;
    gap: 10px;
  }
  .contact-icons svg { width: 24px; height: 24px; }
  .contact-phone {
    position: absolute;
    top: 576px;
    width: 100%;
    font-size: 25px;
    color: var(--text-grey);
  }
  .contact-line {
    position: absolute;
    width: 100%;
    font-size: 18.5px;
    color: var(--text-grey);
  }
  .contact-email { top: 614px; }
  .contact-web { top: 640px; }
  .back-pattern {
    position: absolute;
    inset: 0;
    background: linear-gradient(160deg, var(--brand-blue-light) 0%, var(--brand-blue) 55%, var(--brand-blue) 100%);
  }
  .back-brand {
    position: absolute;
    left: 240px;
    top: 612px;
    display: flex;
    align-items: center;
    gap: 6px;
    font-family: "Montserrat", sans-serif;
    font-weight: 700;
    font-size: 13px;
    color: var(--card-white);
  }
  .back-brand-dot {
    width: 16px;
    height: 16px;
    border-radius: 50%;
    background: var(--card-white);
  }
</style>
</head>
<body>
<main class="stage">
  <section class="card card-front">
    <h1 class="person-name">MARCUS PELLOW</h1>
    <p class="person-title">President</p>

    <div class="brand-lockup">
      <span class="brand-dot"></span>
      <span class="brand-name">Rollers &amp; Glides.com</span>
    </div>

    <div class="contact-icons" aria-hidden="true">
      <svg viewBox="0 0 24 24" class="icon-phone">
        <path fill="#1f4b9f" d="M3 8c0-3 4-5 9-5s9 2 9 5v2h-5V8H8v2H3z"/>
        <rect x="5" y="11" width="14" height="10" rx="2" fill="#1f4b9f"/>
        <circle cx="12" cy="16" r="2.5" fill="#fff"/>
      </svg>
      <svg viewBox="0 0 24 24" class="icon-mail">
        <rect x="2" y="6" width="20" height="14" fill="#1f4b9f"/>
        <path d="M2 6l10 8 10-8" fill="none" stroke="#fff" stroke-width="1.6"/>
      </svg>
      <svg viewBox="0 0 24 24" class="icon-globe">
        <circle cx="12" cy="12" r="10" fill="#1f4b9f"/>
        <path d="M7 7c3 1 3 4 1 6s1 5 3 6M14 5c2 2 5 3 4 6s-3 2-2 5" fill="none" stroke="#fff" stroke-width="1.6"/>
      </svg>
    </div>
    <p class="contact-phone">480.915.2267</p>
    <p class="contact-line contact-email">Marcus@rollersandglides-demo.com</p>
    <p class="contact-line contact-web">www.rollersandglides-demo.com</p>
  </section>

  <section class="card card-back">
    <div class="back-pattern" role="img" aria-label="Embossed repeating brand icon pattern on blue, fading from light to dark"></div>
    <div class="back-brand">
      <span class="back-brand-dot"></span>
      <span>Rollers &amp; Glides.com</span>
    </div>
  </section>
</main>
</body>
</html>
```